Sparrow Haulage needs a business card design.

Design a double-sided business card for new freight business. On the front, would like to see our logo along with the following info:

Martin Obuya
CEO/FOUNDER
555-206-7142
martinobuya@sparrow-haulage.example

On the reverse side, we would like to use the graphic image of our logo only without the Sparrow Haulage name.

```html
<!DOCTYPE html>
<html lang="en">
<head>
<meta charset="utf-8">
<title>Sparrow Haulage – Business Card</title>
<link rel="stylesheet" href="https://fonts.googleapis.com/css2?family=Arimo:wght@400;700&display=swap">
<style>
  :root {
    --backdrop: #555555;
    --paper: #ffffff;
    --navy: #000055;
    --red: #b30000;
    --ink: #2a2a2a;
  }
  * { margin: 0; padding: 0; box-sizing: border-box; }
  html, body { width: 1065px; height: 1200px; overflow: hidden; }
  body {
    background: var(--backdrop);
    font-family: "Arimo", Arial, sans-serif;
    position: relative;
  }
  .card {
    position: absolute;
    width: 583px;
    height: 363px;
    box-shadow: 3px 3px 4px rgba(0,0,0,0.55);
  }
  .card-front {
    left: 292px; top: 218px;
    background: var(--paper);
    border-radius: 0 182px 182px 0;
  }
  .card-back {
    left: 263px; top: 623px;
    background: var(--navy);
    border-radius: 182px 0 0 182px;
  }
  .brand {
    position: absolute;
    left: 44px; top: 92px;
    display: flex; align-items: center; gap: 12px;
  }
  .brand-mark {
    width: 26px; height: 26px;
    background: var(--navy);
  }
  .brand-name {
    font-weight: 700;
    font-size: 27px;
    letter-spacing: 3px;
    color: var(--navy);
    text-transform: uppercase;
  }
  .person {
    position: absolute;
    left: 136px; top: 173px;
  }
  .person-name {
    font-weight: 700;
    font-size: 25px;
    line-height: 1;
    text-transform: uppercase;
  }
  .person-name .first { color: var(--navy); }
  .person-name .last { color: var(--red); }
  .person-title {
    margin-top: 2px;
    font-size: 17.5px;
    color: var(--ink);
  }
  .contacts {
    position: absolute;
    left: 137px; top: 245px;
    list-style: none;
  }
  .contacts li {
    display: flex; align-items: center;
    height: 21.5px;
    font-size: 16px;
    color: var(--ink);
  }
  .contacts svg {
    width: 16px; height: 16px;
    margin-right: 7px;
    fill: var(--red);
  }
  .web-name { color: var(--navy); }
  .web-tld-part { color: var(--red); }
  .back-mark {
    position: absolute;
    left: 50%; top: 50%;
    width: 96px; height: 96px;
    transform: translate(-50%, -50%);
    background: var(--red);
  }
</style>
</head>
<body>
  <section class="card card-front">
    <div class="brand">
      <span class="brand-mark"></span>
      <span class="brand-name">Sparrow Haulage</span>
    </div>

    <div class="person">
      <p class="person-name"><span class="first">Martin</span> <span class="last">Obuya</span></p>
      <p class="person-title">CEO/FOUNDER</p>
    </div>

    <ul class="contacts">
      <li>
        <svg viewBox="0 0 16 16" aria-hidden="true"><path d="M3.5 1.5l2.3 2.6-1.3 1.9c.8 2 2.3 3.6 4.4 4.5l1.9-1.3 2.6 2.3-1.4 2.5C6.5 13.8 2 9.3 1 3z"/><path d="M9.5 2a4.5 4.5 0 0 1 4.5 4.5h-1.2A3.3 3.3 0 0 0 9.5 3.2zM9.5 4.4a2.1 2.1 0 0 1 2.1 2.1h-1.1a1 1 0 0 0-1-1z"/></svg>
        <span>555-206-7142</span>
      </li>
      <li>
        <svg viewBox="0 0 16 16" aria-hidden="true"><path d="M0 3h16v10H0z" fill="var(--red)"/><path d="M0.5 3.5L8 9l7.5-5.5M0.5 12.5l5.5-5M15.5 12.5l-5.5-5" stroke="#fff" stroke-width="1" fill="none"/></svg>
        <span>martinobuya@sparrow-haulage.example</span>
      </li>
      <li>
        <svg viewBox="0 0 16 16" aria-hidden="true"><circle cx="8" cy="8" r="7.5"/><g stroke="#fff" stroke-width="0.9" fill="none"><ellipse cx="8" cy="8" rx="3" ry="7"/><path d="M1 8h14M8 1v14M2 4.5h12M2 11.5h12"/></g></svg>
        <span>www.<span class="web-name">sparrow</span>-<span class="web-tld-part">haulage</span>.example</span>
      </li>
    </ul>
  </section>

  <section class="card card-back">
    <span class="back-mark" role="img" aria-label="Company mark"></span>
  </section>
</body>
</html>
```